Letter and Envelope Design For Harborline Realty

Please design a letter and an envelope incorporating our logo (See Attached). We are also launched a business card contest. Since we want them to match, please feel free to submit a design for both the business card and also the letter design and envelope.

Requirements
Must have
• The envelope, the letter and the business cards must match somehow connecting the designs. We want them to have something that holds them together besides the logo.

```html
<!DOCTYPE html>
<html lang="en">
<head>
<meta charset="utf-8">
<title>Harborline Realty Stationery</title>
<link href="https://fonts.googleapis.com/css2?family=Montserrat:wght@500;600&family=Open+Sans:wght@400;600;700&display=swap" rel="stylesheet">
<style>
  :root {
    --navy: #0b1a8c;
    --grey: #5a5a5e;
    --paper: #f5f5f7;
    --text: #6b6b6f;
    --stage: #e4e5e7;
  }
  * { box-sizing: border-box; margin: 0; padding: 0; }
  html, body { width: 1200px; height: 825px; overflow: hidden; }
  body {
    background: var(--stage);
    font-family: "Open Sans", Arial, sans-serif;
    position: relative;
  }
  .sheet { position: absolute; background: var(--paper); overflow: hidden; }
  .wave { position: absolute; left: 0; bottom: 0; width: 100%; display: block; }

  .brand-mark {
    display: flex; align-items: center; gap: 6px;
    font-family: "Montserrat", Arial, sans-serif;
    font-weight: 600; color: var(--navy); letter-spacing: 1.2px;
    text-transform: uppercase; white-space: nowrap;
  }
  .brand-mark .dot { border: 2px solid var(--navy); border-radius: 50%; flex: none; }

  /* Letterhead */
  .letter { left: 80px; top: 82px; width: 467px; height: 660px; }
  .letter .brand-mark { position: absolute; left: 32px; top: 44px; font-size: 11px; }
  .letter .brand-mark .dot { width: 18px; height: 18px; }
  .letter-contact {
    position: absolute; left: 328px; top: 40px; padding-left: 7px;
    border-left: 1px solid var(--grey);
    font-size: 7px; line-height: 9px; color: var(--grey);
  }
  .letter-contact span { display: block; }
  .letter-contact span::before {
    content: ""; display: inline-block; width: 4px; height: 4px;
    background: var(--navy); border-radius: 1px; margin-right: 4px; vertical-align: 1px;
  }
  .salutation {
    position: absolute; left: 38px; top: 134px;
    font-family: Arial, sans-serif; font-weight: 700; font-size: 11.5px; color: #4a4a4e;
  }
  .letter-body { position: absolute; left: 38px; top: 166px; width: 392px; }
  .letter-body p {
    font-size: 9.2px; line-height: 12.3px; color: var(--text);
    text-align: justify; margin-bottom: 12px;
  }
  .signature {
    position: absolute; left: 38px; top: 460px; width: 90px; height: 42px;
    background: linear-gradient(90deg, #e2e2e6, #ececef); border-radius: 3px;
  }
  .footer-block {
    position: absolute; right: 42px; bottom: 5px; text-align: right;
    color: #fff; font-size: 7px; line-height: 9px; white-space: nowrap;
  }
  .footer-block strong { font-weight: 700; font-size: 7.3px; }

  /* Business cards */
  .card { position: absolute; top: 302px; width: 198px; height: 113px; }
  .card-front { left: 642px; background: var(--paper); overflow: hidden; }
  .card-front .brand-mark { position: absolute; right: 9px; top: 40px; font-size: 7px; letter-spacing: 0.8px; }
  .card-front .brand-mark .dot { width: 11px; height: 11px; border-width: 1.5px; }
  .card-person { position: absolute; left: 0; top: 40px; padding-left: 9px; border-left: 3px solid var(--navy); }
  .card-person .name { font-size: 6.5px; font-weight: 600; color: var(--navy); text-transform: uppercase; }
  .card-person .role { font-size: 5px; color: var(--grey); }
  .card-details { position: absolute; left: 9px; top: 61px; font-size: 4.8px; line-height: 7px; color: var(--grey); }
  .card-details .gap { height: 5px; }
  .card-web { position: absolute; right: 16px; bottom: 4px; font-size: 5px; color: #fff; }
  .card-back {
    left: 863px; background: var(--navy);
    display: flex; align-items: center; justify-content: center;
  }
  .card-back .brand-mark { color: #fff; font-size: 8px; }
  .card-back .brand-mark .dot { width: 16px; height: 16px; border-color: #fff; }

  /* Envelope */
  .envelope { left: 584px; top: 445px; width: 536px; height: 297px; }
  .flap { position: absolute; left: 0; top: 0; width: 100%; height: 65px; display: block; }
  .flap-web {
    position: absolute; left: 0; right: 0; top: 29px; text-align: center;
    color: #fff; font-size: 7px; letter-spacing: 0.8px; transform: rotate(180deg);
  }
  .sender-mark {
    position: absolute; left: 34px; top: 125px;
    font-family: "Open Sans", Arial, sans-serif; font-weight: 600;
    font-size: 12px; color: var(--navy); letter-spacing: 0.6px; text-transform: uppercase;
  }
  .address-box {
    position: absolute; left: 34px; top: 180px; width: 206px; height: 62px;
    background: #f0f0f2; border-radius: 3px; padding: 14px 8px 0;
  }
  .address-box span { display: block; border-bottom: 1px dotted #b8b8bc; height: 11px; }
  .envelope .footer-block { right: 40px; bottom: 5px; }
</style>
</head>
<body>

<section class="sheet letter" aria-label="Letterhead">
  <div class="brand-mark"><span class="dot"></span>Harborline Realty</div>
  <div class="letter-contact">
    <span>555-014-2290</span>
    <span>info@harborline.com</span>
    <span>info@harborline.com</span>
  </div>
  <h1 class="salutation">Dear Mr. Carter,</h1>
  <div class="letter-body">
    <p>Lorem Ipsum is simply dummy text of the printing and typesetting industry. Lorem Ipsum has been the industry's standard dummy text ever since the 1500s, when an unknown printer took a galley of type and scrambled it to make a type specimen book. It has survived not only five centuries, but also the leap into electronic typesetting, remaining essentially unchanged.</p>
    <p>The standard chunk of Lorem Ipsum used since the 1500s is reproduced below for those interested. Sections 1.10.32 and 1.10.33 from "de Finibus Bonorum et Malorum" by Varrin are also reproduced in their exact original form, accompanied by English versions from the 1914 translation by H. Ellery</p>
    <p>Lorem Ipsum is simply dummy text of the printing and typesetting industry. Lorem Ipsum has been the industry's standard dummy text ever since the 1500s, when an unknown printer took a galley of type and scrambled it to make a type specimen book. It has survived not only five centuries, but also the leap into electronic typesetting, remaining essentially unchanged. It was popularised in the</p>
    <p>Lorem Ipsum is simply dummy text of the printing and typesetting industry. Lorem Ipsum has been the industry's standard dummy text ever since the 1500s, when an unknown printer took a galley of type and scrambled it to make a type specimen book. It has survived not only five centuries, but also the leap into electronic typesetting, remaining essentially unchanged. It was popularised in the</p>
  </div>
  <div class="signature" role="img" aria-label="Handwritten signature"></div>
  <svg class="wave" viewBox="0 0 467 80" height="80" preserveAspectRatio="none" aria-hidden="true">
    <path d="M0 22 C50 60 140 62 230 40 C320 20 420 10 467 12 L467 22 C420 20 320 30 230 50 C140 72 50 70 0 32 Z" fill="var(--grey)"/>
    <path d="M0 36 C50 74 140 76 230 54 C320 34 420 24 467 26 L467 80 L0 80 Z" fill="var(--navy)"/>
  </svg>
  <div class="footer-block"><strong>Harborline Realty</strong><br>Po. box 201, Street Name, City Name, Zip Code - 00000</div>
</section>

<section class="sheet card card-front" aria-label="Business card front">
  <div class="brand-mark"><span class="dot"></span>Harborline Realty</div>
  <div class="card-person">
    <div class="name">Daniel Reyes</div>
    <div class="role">Director</div>
  </div>
  <div class="card-details">
    <div>555-014-2290</div>
    <div>info@harborline.com</div>
    <div class="gap"></div>
    <div>Po. box 201, Street Name,</div>
    <div>City Name, Zip Code - 00000</div>
  </div>
  <svg class="wave" viewBox="0 0 198 28" height="28" preserveAspectRatio="none" aria-hidden="true">
    <path d="M0 10 C30 24 80 24 120 14 C150 6 180 0 198 2 L198 7 C180 6 150 12 120 19 C80 28 30 28 0 15 Z" fill="var(--grey)"/>
    <path d="M0 17 C30 30 80 30 120 21 C150 14 180 8 198 10 L198 28 L0 28 Z" fill="var(--navy)"/>
  </svg>
  <div class="card-web">www.harborline.com</div>
</section>

<section class="card card-back" aria-label="Business card back">
  <div class="brand-mark"><span class="dot"></span>Harborline Realty</div>
</section>

<section class="sheet envelope" aria-label="Envelope">
  <svg class="flap" viewBox="0 0 536 65" preserveAspectRatio="none" aria-hidden="true">
    <path d="M0 65 L8 14 C10 4 14 0 24 0 L512 0 C522 0 526 4 528 14 L536 65 Z" fill="var(--navy)"/>
  </svg>
  <div class="flap-web">www.harborline.com</div>
  <div class="sender-mark">Wayfield Partners</div>
  <div class="address-box"><span></span><span></span><span></span><span></span></div>
  <svg class="wave" viewBox="0 0 536 80" height="80" preserveAspectRatio="none" aria-hidden="true">
    <path d="M0 22 C60 60 170 62 280 40 C380 20 480 10 536 12 L536 22 C480 20 380 30 280 50 C170 72 60 70 0 32 Z" fill="var(--grey)"/>
    <path d="M0 36 C60 74 170 76 280 54 C380 34 480 24 536 26 L536 80 L0 80 Z" fill="var(--navy)"/>
  </svg>
  <div class="footer-block"><strong>Harborline Realty</strong><br>Po. box 201, Street Name, City Name, Zip Code - 00000</div>
</section>

</body>
</html>
```